Doctor to Patient Management Website

I need a design for a health management website that connects doctors to patients. The website will consist of: A main page mainly describing our goal, services, and initiatives towards (Who we are AKA "About Us", Our services, Contact Us, Quick Links for health tips, Language selection, Find a doctor, search bar, Member Login Section, small glossary section below with links to all entities mentioned prior, Help section (Helpful tips and tutorials, Used to request help from admin, customer service, to resolve issues or get assistance). A profile page with two types:1) Doctor Profile: Doctor Personal info (First, Last, Middle Name, Title), Clinic, Hospital Info, Department, Credentials, Years of Experience, Patients rating, #Patients seen during the current week, #Patients seen in total, Picture, Link to email doctor, Link to print doctor's profile). Tabs for "About Me", "Contact Info", "Ratings & Comments", "Documents" (To be downloaded and uploaded by patient), "Patients (List of Patients alphabetical order by name)", "Calendar" (to see doctor's availability for booking) underneath all links. 2) Patient profile: About me, Personal Info, Height, Weight, Blood Type, Age, DOB, Name, etc..., Message and email link.Picture of patient with menu made of "Personal Data", "Biometrics", "Allergies", "Illnesses", "Medications", "Medical Procedures", "Doctors" treating the patient, "Documents" (To be downloaded and uploaded by patient). Underneath all, other patients he or she is related to (For example: family member, so patient can't connect to other patients who are family members)3) Login section: New Users will have option to register using:First Name (Required), Last Name, Middle (not required), Address (Not required), City (Required), Country (Required), Email (Not required), Phone Number (Required), Choose UserName, Password, Account Type (Doctor or Patient). Once registered, they will log in using UserName, Password, and Account_Type.Curent Users will log in using UserName, Password, and Account_Type and option to retrieve username or password.Pages to include (Login Page - Registration Page - Retrieve Username and Reset Password Page)Please see link below:https://plumcrate-adwerks.net/importance-claiming-vantorix-quibble-zarn/Pictures are attached to this project as an inspirationFYI: Dummy text can be used to fill in the business, services, and descriptive information. Feel free to include your own ideas in the layout, design, categories, patterns, and more to and showcase your talent. Design and pictures provided are available as source of ideas.

Target Market(s)

Age: 21+ / Family Oriented / Medical Sector / Metropolitan Area / Educated and non Educated Users

Industry/Entity Type

Health Care

Number of Pages Required

5+ page

Font styles to use
Sans Serif

Colors

Designer to choose colors to be used in the design.

Requirements
Must have
• Thin layer design
• Simple font - No serif
• Clean menu with light but solid colors (No Gradient effect)
Nice to have
• Different color themes (2 or 3) can be combined
• Sample pictures for illustration (either as an ad or to go with the flow of your design)
• Dashboard Feel (Suggested but not required)
Should not have
• Artistic fonts - with Serif
• Dark color themes

```html
<!DOCTYPE html>
<html lang="en">
<head>
<meta charset="utf-8">
<title>Velmora – Doctor to Patient Care</title>
<link href="https://fonts.googleapis.com/css2?family=Montserrat:wght@400;500;600;700&family=Open+Sans:wght@400;600&display=swap" rel="stylesheet">
<style>
:root{
  --ink:#4a4a4a;
  --ink-soft:#666;
  --muted:#8a8a8a;
  --accent:#7cc0ea;
  --page:#f8f8f8;
  --white:#fff;
  --line:#dcdcdc;
  --blue:#d6eafc;
  --pink:#f6c6cb;
  --yellow:#fdf2b4;
  --lilac:#e2dbf8;
  --tab-pink:#f4c1c6;
  --tab-blue:#cfe6f8;
  --footer:#ececec;
}
*{box-sizing:border-box;margin:0;padding:0}
html,body{width:1200px;height:3214px;overflow:hidden}
body{background:var(--page);font-family:"Open Sans",Arial,sans-serif;color:var(--ink);position:relative}
.abs{position:absolute}
h1,h2,h3,h4,.brand{font-family:"Montserrat",Arial,sans-serif}
.btn{position:absolute;background:var(--accent);color:#fff;font-family:"Montserrat",Arial,sans-serif;font-size:12px;letter-spacing:.5px;text-transform:uppercase;display:flex;align-items:center;justify-content:center}

/* top bar */
.topbar{left:0;top:0;width:1200px;height:32px;background:var(--white);border-bottom:1px solid #eee}
.lang{left:171px;top:9px;font-size:12px;color:var(--ink-soft);display:flex;align-items:center;gap:6px}
.lang .flag{width:14px;height:9px;background:#c9423f;display:inline-block}
.tab{top:0;height:32px;font-family:"Montserrat",Arial,sans-serif;font-size:12px;font-weight:600;display:flex;align-items:center;justify-content:center;color:#6a5a5a}
.tab-login{left:778px;width:136px;background:var(--tab-pink);clip-path:polygon(8px 0,100% 0,100% 100%,0 100%)}
.tab-find{left:906px;width:122px;background:var(--tab-blue);clip-path:polygon(8px 0,100% 0,calc(100% - 8px) 100%,0 100%)}

/* nav */
.nav{left:0;top:32px;width:1200px;height:72px;background:var(--white)}
.brand{left:171px;top:17px;font-size:36px;font-weight:700;color:#555;letter-spacing:.5px}
.menu{left:380px;top:28px;display:flex;gap:0;font-family:"Montserrat",Arial,sans-serif;font-size:13px;font-weight:500;color:#555}
.menu span{position:absolute;white-space:nowrap}
.search{left:840px;top:24px;width:188px;height:26px;background:#f1f1f1;border-radius:13px;font-size:11px;color:#aaa;padding:6px 14px}
.search svg{position:absolute;right:10px;top:7px}

/* hero */
.hero{left:0;top:104px;width:1200px;height:556px;background:linear-gradient(90deg,#cfd9e2 0%,#e9f1f8 40%,#f2f7fb 60%,#c9ccd1 100%)}
.hero-title{left:0;top:198px;width:1200px;text-align:center;font-size:62px;font-weight:700;color:#5b5b5b}
.hero .btn{left:546px;top:286px;width:108px;height:36px}
.dots{left:578px;top:518px;display:flex;gap:5px}
.dots i{width:7px;height:7px;border-radius:50%;background:#bbb;display:block}
.dots i:first-child{background:#e3e3e3}

/* services */
.section-title{left:0;width:1200px;text-align:center;font-size:36px;font-weight:600;color:#4a4a4a}
.lead{left:0;width:1200px;text-align:center;font-size:15px;line-height:23px;color:#555}
.service{top:860px;width:205px;height:293px;text-align:center}
.service svg{margin-top:32px}
.service h3{font-size:16px;font-weight:500;color:#444;margin-top:26px}
.service p{font-size:12.5px;line-height:21px;color:#555;margin:14px 22px 0}

/* about */
.about{left:171px;top:1215px;width:855px;height:437px;background:var(--white);border:1px solid var(--line)}
.about .photo{left:0;top:0;width:365px;height:435px;background:linear-gradient(90deg,#d4d8dc,#f3f4f5)}
.about h2{left:399px;top:66px;font-size:34px;font-weight:600;color:#444}
.about p{left:400px;top:130px;width:400px;font-size:12.5px;line-height:21.5px;color:#555}
.about .btn{left:401px;top:325px;width:107px;height:37px}

/* tips */
.tips{left:171px;top:1738px;width:343px;height:381px;background:var(--pink)}
.tips h2{left:26px;top:28px;font-size:32px;font-weight:600;color:#444}
.tips ul{left:26px;top:98px;list-style:none;font-family:"Montserrat",Arial,sans-serif;font-size:12px;font-weight:500;color:#4a4a4a}
.tips li{height:31.5px}
.tips li::before{content:"•";margin-right:6px}
.help{left:536px;top:1738px;width:490px;height:381px;background:var(--white);border:1px solid var(--line)}
.help .photo{left:0;top:0;width:240px;height:379px;background:linear-gradient(135deg,#7c6f62,#cfc8bf 60%,#e8e6e3)}
.help h3{left:271px;top:50px;width:200px;font-size:16px;line-height:24px;font-weight:600;color:#444}
.help p{left:271px;top:136px;width:195px;font-size:12.5px;line-height:21.5px;color:#555}
.help .btn{left:273px;top:301px;width:129px;height:37px}

/* tutorials */
.tutorial{top:2254px;height:405px;background:var(--white);border:1px solid var(--line);text-align:center}
.tutorial .photo{width:100%;height:185px}
.tutorial h3{font-size:17px;font-weight:600;color:#444;margin-top:34px}
.tutorial p{font-size:12.5px;line-height:21.5px;color:#555;margin:20px 22px 0}

/* footer */
.footer{left:0;top:2777px;width:1200px;height:437px;background:var(--footer)}
.fcol{top:57px;font-size:12.5px;line-height:22.5px;color:#555}
.fcol h4{font-size:16px;font-weight:600;color:#444;margin-bottom:12px;display:flex;align-items:center;gap:10px}
.fcol h4.gap{margin-top:28px}
.rule{left:171px;top:358px;width:855px;height:1px;background:#cfcfcf}
.legal{top:399px;font-size:12.5px;color:#555}
</style>
</head>
<body>

<header>
  <div class="abs topbar">
    <div class="abs lang">Language <span class="flag"></span> <svg width="8" height="5"><path d="M0 0l4 5 4-5z" fill="#888"/></svg></div>
    <a class="abs tab tab-login">Member Login</a>
    <a class="abs tab tab-find">Find a Doctor</a>
  </div>
  <div class="abs nav">
    <div class="abs brand">Velmora</div>
    <nav class="abs menu">
      <span style="left:0">Home</span>
      <span style="left:66px">About</span>
      <span style="left:143px">Patients</span>
      <span style="left:231px">Reviews</span>
      <span style="left:319px">FAQ</span>
      <span style="left:383px">Contact</span>
    </nav>
    <div class="abs search">Search
      <svg width="12" height="12" viewBox="0 0 12 12"><circle cx="5" cy="5" r="3.8" fill="none" stroke="#777" stroke-width="1.5"/><path d="M8 8l3 3" stroke="#777" stroke-width="1.6"/></svg>
    </div>
  </div>
</header>

<section class="abs hero" role="img" aria-label="Photo of a doctor reassuring a smiling patient in a bright clinic">
  <h1 class="abs hero-title" style="top:94px">Velmora</h1>
  <a class="btn">Read More</a>
  <div class="abs dots"><i></i><i></i><i></i></div>
</section>

<section class="services">
  <h2 class="abs section-title" style="top:716px">Our Services</h2>
  <p class="abs lead" style="top:774px">Lorem ipsum dolor sit amet, consectetur adipiscing elit<br>tempor incididunt ut labore et dolore magnliqua.</p>

  <div class="abs service" style="left:171px;background:var(--blue)">
    <svg width="80" height="80" viewBox="0 0 80 80" fill="none" stroke="#555" stroke-width="2"><rect x="10" y="8" width="22" height="48" rx="11" transform="rotate(-40 21 32)"/><path d="M12 34l18-15"/><ellipse cx="54" cy="56" rx="20" ry="8"/><path d="M34 56v7c0 4 9 8 20 8s20-4 20-8v-7"/></svg>
    <h3>Service Name</h3>
    <p>Lorem ipsum dolorosit amet, consectetur loadipi scing elit tempor loincid idunt ut labore edo</p>
  </div>
  <div class="abs service" style="left:390px;background:var(--pink)">
    <svg width="80" height="80" viewBox="0 0 80 80" fill="none" stroke="#555" stroke-width="2"><circle cx="40" cy="26" r="13"/><path d="M16 74v-12c0-10 10-16 24-16s24 6 24 16v12z"/><path d="M34 46l6 10 6-10M30 50v10a5 5 0 0 0 10 0"/></svg>
    <h3>Service Name</h3>
    <p>Lorem ipsum dolorosit amet, consectetur loadipi scing elit tempor loincid idunt ut labore edo</p>
  </div>
  <div class="abs service" style="left:606px;background:var(--yellow)">
    <svg width="80" height="80" viewBox="0 0 80 80" fill="none" stroke="#555" stroke-width="2"><rect x="16" y="12" width="48" height="62" rx="3"/><rect x="30" y="7" width="20" height="10" rx="2"/><rect x="22" y="22" width="36" height="46"/><path d="M36 34h8v8h8v8h-8v8h-8v-8h-8v-8h8z"/></svg>
    <h3>Service Name</h3>
    <p>Lorem ipsum dolorosit amet, consectetur loadipi scing elit tempor loincid idunt ut labore edo</p>
  </div>
  <div class="abs service" style="left:823px;background:var(--lilac)">
    <svg width="80" height="80" viewBox="0 0 80 80" fill="none" stroke="#555" stroke-width="2"><circle cx="40" cy="24" r="12"/><path d="M18 74V60c0-9 9-14 22-14s22 5 22 14v14z"/><path d="M34 46l6 8 6-8M40 54v20"/></svg>
    <h3>Service Name</h3>
    <p>Lorem ipsum dolorosit amet, consectetur loadipi scing elit tempor loincid idunt ut labore edo</p>
  </div>
</section>

<section class="abs about">
  <div class="abs photo" role="img" aria-label="Portrait of a senior doctor in a white coat with a stethoscope"></div>
  <h2 class="abs">About Us</h2>
  <p class="abs">Sed ut perspiciatis unde omnis iste natus error sit voluptatem accusantium doloremque laudantium, totam rem aperiam, eaque quae ab illo inventore veritatis et quasi architecto beatae vitae di sunt explicabo. Nemo enim ipsam voluptatem quia voluptas sit aspernatur aut odit aut fugit, sed quia consequuntur magni dolor qui ratione voluptatem sequi nesciunt. Neque porro quisquam est, dolorem ipsum quia dolor sit amet, consectetur, adipisci velit, sed non numquam eius modi tempora incidunt ut labor</p>
  <a class="btn">Read More</a>
</section>

<section>
  <div class="abs tips">
    <h2 class="abs">Health Tips</h2>
    <ul class="abs">
      <li>Maecenas tempus ipsum eget luctus</li>
      <li>Nullam nec metus eu dolor vulputate</li>
      <li>Vestibulum sollicitudin sem sagittis,</li>
      <li>Donec sit amet nisi at massa consequat</li>
      <li>Nulla varius turpis iaculis tincidunt</li>
      <li>Duis fringilla nisi vestibulum enliquet,</li>
      <li>Cras mattis turpis eu quam euismod</li>
      <li>Quisque vel leo eu mt mol</li>
    </ul>
  </div>
  <div class="abs help">
    <div class="abs photo" role="img" aria-label="Photo of a doctor with glasses seated at his desk"></div>
    <h3 class="abs">Sed ut perspiciatund emniste natus error sit voluptatelorusantiu</h3>
    <p class="abs">Sed ut perspiciatis unde omnis te natus error sit voluptatelorm accusantium dolorequelaudanti um, totam rem aperiam, eaque quae ab illo inventore veritatist quasi architecto beatae vitae di sunt explicabo.mo eni</p>
    <a class="btn">Request Help</a>
  </div>
</section>

<section>
  <h2 class="abs section-title" style="top:2192px">Tutorials</h2>
  <div class="abs tutorial" style="left:171px;width:275px">
    <div class="photo" role="img" aria-label="Photo of a doctor consulting with a patient at a desk" style="background:linear-gradient(135deg,#c9a792,#eef0f2 55%,#dfe6ec)"></div>
    <h3>Voluptatelorntiu</h3>
    <p>Sed ut perspiciatis unde omniste natus error sit voluptatelorm accu santium dolorequelaudantium, totam rem aperiam, eaque quae ab illo inventore veritatist qua</p>
  </div>
  <div class="abs tutorial" style="left:463px;width:272px">
    <div class="photo" role="img" aria-label="Photo of medical staff reviewing a tablet in a hospital corridor" style="background:linear-gradient(135deg,#2f5fa0,#8fb0d6 50%,#d8e2ee)"></div>
    <h3>Voluptatelorntiu</h3>
    <p>Sed ut perspiciatis unde omniste natus error sit voluptatelorm accu santium dolorequelaudantium, totam rem aperiam, eaque quae ab illo inventore veritatist qua</p>
  </div>
  <div class="abs tutorial" style="left:752px;width:274px">
    <div class="photo" role="img" aria-label="Image of hands using a tablet with floating health icons" style="background:linear-gradient(135deg,#eef5f8,#8fc8d8 55%,#3e8fa8)"></div>
    <h3>Voluptatelorntiu</h3>
    <p>Sed ut perspiciatis unde omniste natus error sit voluptatelorm accu santium dolorequelaudantium, totam rem aperiam, eaque quae ab illo inventore veritatist qua</p>
  </div>
  <a class="btn" style="left:531px;top:2700px;width:138px;height:37px">Request Help</a>
</section>

<footer class="abs footer">
  <div class="abs fcol" style="left:171px">
    <h4><svg width="16" height="18" viewBox="0 0 16 18" fill="none" stroke="#666" stroke-width="1.4"><path d="M8 17s6-6 6-10A6 6 0 0 0 2 7c0 4 6 10 6 10z"/><circle cx="8" cy="7" r="2"/></svg>Contact Us</h4>
    Velmora<br>Lorem iSum Dummt67<br>Eastbrook&nbsp;&nbsp;&nbsp; dummy782<br>EB4 7QX
    <h4 class="gap"><svg width="18" height="13" viewBox="0 0 18 13" fill="none" stroke="#666" stroke-width="1.4"><rect x="1" y="1" width="16" height="11"/><path d="M1 1l8 6 8-6"/></svg>Email</h4>
    info@velmora-care.example
    <h4 class="gap"><svg width="16" height="16" viewBox="0 0 16 16" fill="none" stroke="#666" stroke-width="1.4"><path d="M3 1l3 3-2 2c1 3 3 5 6 6l2-2 3 3-2 2C7 15 1 9 1 3z"/></svg>Phone</h4>
    01632 960418
  </div>
  <div class="abs fcol" style="left:392px">
    <h4>Patient Resources</h4>
    Lorem ipsum dolor<br>Consectetur adipiscin<br>Do eiusmodt
    <h4 class="gap">General Information</h4>
    Lorem ipsum dolor<br>Consectetur adipiscin<br>Do eiusmodt
  </div>
  <div class="abs fcol" style="left:641px">
    <h4>Quick Links</h4>
    Sed ut perspiciatis<br>H iste natus error sit<br>Gptatem accusantium dolo<br>Rremque laudantium,<br>Rotam rem aperiam, ea<br>Sed ut perspiciatis u<br>H iste natus error
  </div>
  <div class="abs fcol" style="left:866px">
    <h4>Glossary</h4>
    Sed ut perspiciatis und<br>Gptatem accusantium dolo<br>Rremque laudantium,<br>Rotam rem aperiam, ea<br>Sed ut perspiciatide omn<br>H iste natus error sit volu<br>Gptatem accum dolo<br>Rremque laudantium,
  </div>
  <div class="abs rule"></div>
  <div class="abs legal" style="left:171px">© 2019 Velmora. All rights reserved.</div>
  <div class="abs legal" style="left:840px">Terms of Use&nbsp;&nbsp;&nbsp;|&nbsp;&nbsp;&nbsp;Privacy Policy</div>
</footer>

</body>
</html>
```